Road Construction Company needs business cards

We would like a new business card designed for our business.

We're a road construction company based in Qld, Australia.

Can the business card please have the following information on it.

Name: Warren Halbeck
Position: General Manager
Phone: 0472 915 348
Email: warren.halbeck@tovrin.com.au
Address: 87 Marrow Ave, Pendlebay, QLD, 4023
Website: www.tovrin.com.au

Visually we'd like the card to be professional and simple.

Attached is our logo.

Our website is www.tovrin.com.au

Target Market(s)

Men aged 25-60

Contact Information for Business Card

As listed in project description

Font styles to use
Serif

Requirements
Must have
• Large logo on back of card

```html
<!DOCTYPE html>
<html lang="en">
<head>
<meta charset="utf-8">
<title>Tovrin Business Card</title>
<link rel="stylesheet" href="https://fonts.googleapis.com/css2?family=Poppins:wght@400;700&display=swap">
<style>
  :root {
    --backdrop: #979797;
    --card: #fbfbfb;
    --navy: #0c4f9e;
    --sky: #3f9bd6;
    --ink: #555a5f;
    --rule: #d4d6d8;
  }
  * { margin: 0; padding: 0; box-sizing: border-box; }
  html, body { width: 1200px; height: 1000px; overflow: hidden; }
  body {
    background: var(--backdrop);
    position: relative;
    font-family: "Poppins", sans-serif;
  }
  .card {
    position: absolute;
    width: 615px;
    height: 350px;
    background: var(--card);
  }
  .card--front { left: 292px; top: 121px; }
  .card--back  { left: 293px; top: 537px; }

  .brand {
    position: absolute;
    font-weight: 700;
    color: var(--navy);
    letter-spacing: 1px;
    line-height: 1;
  }
  .card--front .brand {
    left: 0; right: 0; top: 146px;
    text-align: center;
    font-size: 54px;
  }
  .card--back .brand {
    left: 57px; top: 154px;
    font-size: 34px;
  }

  .divider {
    position: absolute;
    left: 307px; top: 63px;
    width: 1px; height: 232px;
    background: var(--rule);
  }

  .contact {
    position: absolute;
    left: 337px; top: 86px;
    color: var(--ink);
  }
  .contact__name {
    font-weight: 700;
    font-size: 20px;
    color: var(--navy);
    line-height: 1;
    text-transform: uppercase;
  }
  .contact__role {
    font-size: 12.5px;
    color: var(--sky);
    text-transform: uppercase;
    margin-top: 8px;
    line-height: 1;
  }
  .contact__address {
    font-size: 13.5px;
    line-height: 17px;
    margin-top: 15px;
  }
  .contact__list {
    list-style: none;
    margin-top: 16px;
    font-size: 13.5px;
  }
  .contact__list li {
    display: flex;
    align-items: center;
    height: 24px;
  }
  .contact__list svg {
    width: 18px; height: 18px;
    margin-right: 7px;
    flex: none;
  }
</style>
</head>
<body>
  <section class="card card--front">
    <div class="brand">TOVRIN</div>
  </section>

  <section class="card card--back">
    <div class="brand">TOVRIN</div>
    <div class="divider"></div>
    <div class="contact">
      <div class="contact__name">Warren Halbeck</div>
      <div class="contact__role">General Manager</div>
      <div class="contact__address">87 Marrow Ave,<br>Pendlebay, QLD, 4023</div>
      <ul class="contact__list">
        <li>
          <svg viewBox="0 0 24 24" fill="none" stroke="#3f9bd6" stroke-width="1.6" stroke-linejoin="round"><path d="M5 3h4l2 5-2.5 1.5a11 11 0 0 0 6 6L16 13l5 2v4a2 2 0 0 1-2 2A16 16 0 0 1 3 5a2 2 0 0 1 2-2z"/></svg>
          0472 915 348
        </li>
        <li>
          <svg viewBox="0 0 24 24" fill="none" stroke="#3f9bd6" stroke-width="1.6"><rect x="3" y="5" width="18" height="14"/><path d="M3 5l9 8 9-8M3 19l7-7M21 19l-7-7"/></svg>
          warren.halbeck@tovrin.com.au
        </li>
        <li>
          <svg viewBox="0 0 24 24" fill="none" stroke="#3f9bd6" stroke-width="1.6"><circle cx="12" cy="12" r="9"/><ellipse cx="12" cy="12" rx="4" ry="9"/><path d="M3 12h18M5 7h14M5 17h14"/></svg>
          www.tovrin.com.au
        </li>
      </ul>
    </div>
  </section>
</body>
</html>
```